Brivolt Technologies business card design

We need a business card designed with our new logo. it would be great if the card could communicate it is a technology based company.

Target Market(s)

system integrators

Industry/Entity Type

technology, IOT

Contact Information for Business Card

Name, designation, Address, telephone number, email address

Requirements
Must have
• logo and company name
Nice to have
• something to do with technology

```html
<!DOCTYPE html>
<html lang="en">
<head>
<meta charset="utf-8">
<title>Brivolt Technologies – Business Card</title>
<link href="https://fonts.googleapis.com/css2?family=Exo+2:wght@600&family=Roboto+Condensed:wght@300;400;500&display=swap" rel="stylesheet">
<style>
  :root {
    --bg: #e4e4e4;
    --card-front: #f6f6f6;
    --ink: #4a4a4a;
    --ink-dark: #3f3f43;
    --accent: #e8891c;
    --back-top: #4b4b4f;
    --back-bottom: #3b3b3f;
    --back-mark: #2e2e31;
  }
  * { margin: 0; padding: 0; box-sizing: border-box; }
  html, body { width: 1200px; height: 1200px; overflow: hidden; }
  body {
    background: var(--bg);
    font-family: "Roboto Condensed", sans-serif;
    position: relative;
  }
  .card {
    position: absolute;
    left: 262px;
    width: 686px;
    height: 392px;
    border-radius: 22px;
    overflow: hidden;
  }
  .card-front { top: 165px; background: var(--card-front); }
  .card-back {
    top: 653px;
    background: linear-gradient(180deg, var(--back-top), var(--back-bottom));
  }

  .brand {
    position: absolute;
    display: flex;
    align-items: center;
    gap: 10px;
  }
  .brand-square {
    width: 20px;
    height: 20px;
    background: var(--accent);
    flex: none;
  }
  .brand-name {
    font-family: "Roboto Condensed", sans-serif;
    font-weight: 500;
    text-transform: uppercase;
    line-height: 1;
    white-space: nowrap;
  }
  .card-front .brand { left: 78px; top: 182px; width: 282px; }
  .card-front .brand-name { font-size: 22px; color: var(--ink-dark); letter-spacing: 0.5px; }

  .card-back .brand { left: 50%; top: 50%; transform: translate(-50%, -50%); gap: 14px; }
  .card-back .brand-square { width: 28px; height: 28px; background: var(--back-mark); }
  .card-back .brand-name { font-size: 38px; color: var(--back-mark); letter-spacing: 1px; }

  .divider {
    position: absolute;
    left: 375px;
    top: 90px;
    width: 1px;
    height: 222px;
    background: #8c8c8c;
  }
  .contact {
    position: absolute;
    left: 399px;
    top: 93px;
    color: var(--ink);
    font-weight: 300;
    font-size: 18px;
    line-height: 1;
  }
  .contact-name {
    font-family: "Exo 2", sans-serif;
    font-weight: 600;
    font-size: 25px;
    color: var(--accent);
    letter-spacing: 0.3px;
  }
  .contact-title { margin-top: 6px; }
  .contact-address { margin-top: 14px; }
  .contact-address p + p { margin-top: 4px; }
  .contact-lines { margin-top: 15px; list-style: none; }
  .contact-lines li {
    display: flex;
    align-items: center;
    gap: 10px;
    height: 21.5px;
  }
  .contact-lines svg { width: 15px; height: 15px; fill: var(--accent); flex: none; }

  .band {
    position: absolute;
    left: 0;
    bottom: 0;
    width: 100%;
    height: 12px;
    display: flex;
  }
  .band-accent { width: 343px; background: var(--accent); }
  .band-gap { width: 2px; background: #ffffff; }
  .band-dark { flex: 1; background: var(--ink-dark); }
</style>
</head>
<body>

<section class="card card-front">
  <div class="brand">
    <span class="brand-square"></span>
    <span class="brand-name">Brivolt Technologies</span>
  </div>

  <div class="divider"></div>

  <div class="contact">
    <h1 class="contact-name">Daniel Morgan</h1>
    <p class="contact-title">Managing Director</p>
    <div class="contact-address">
      <p>4120 Larkspur Road</p>
      <p>Juneau, Alaska 34581</p>
    </div>
    <ul class="contact-lines">
      <li>
        <svg viewBox="0 0 16 16" aria-hidden="true"><path d="M3.5 1l2.6 3-1.5 1.8c.9 1.9 2.6 3.6 4.5 4.5L10.9 8.8l3.1 2.6-1.6 2.9C7 14.2 1.8 9 1.6 3.6z"/></svg>
        <span>936-555-0142</span>
      </li>
      <li>
        <svg viewBox="0 0 16 16" aria-hidden="true"><path d="M4 1h8v14H4zM5.5 2.8v9.4h5V2.8zM7.2 13.2h1.6v1H7.2z" fill-rule="evenodd"/></svg>
        <span>936-555-0187</span>
      </li>
      <li>
        <svg viewBox="0 0 16 16" aria-hidden="true"><path d="M1 3.5h14v9H1zM2.2 4.6L8 8.8l5.8-4.2v.9L8 9.9 2.2 5.5z" fill-rule="evenodd"/></svg>
        <span>info@brivolt.com</span>
      </li>
      <li>
        <svg viewBox="0 0 16 16" aria-hidden="true"><circle cx="8" cy="8" r="7"/><path d="M5 4.5c1.5.3 2 1.5 1.3 2.6-.8 1 .5 1.9 1.8 1.6 1 .9.2 2.4-.6 3.3M10.5 3.5c-.5 1 .3 1.8 1.5 1.7" stroke="#f6f6f6" stroke-width="1.3" fill="none"/></svg>
        <span>www.brivolt.com</span>
      </li>
    </ul>
  </div>

  <div class="band">
    <span class="band-accent"></span>
    <span class="band-gap"></span>
    <span class="band-dark"></span>
  </div>
</section>

<section class="card card-back">
  <div class="brand">
    <span class="brand-square"></span>
    <span class="brand-name">Brivolt Technologies</span>
  </div>
</section>

</body>
</html>
```